Indy Film Production Company/Studio

We need a business card designed from an existing logo. We are a digital studio/production company that caters to creating genre entertainment, like Action, Horror, and martial arts. The card along with the logo will be used to Brand the company from letter heads to banners. The design will also be used for postcards and Brochures. It should be professional and masculine.
Updates

Thank you to all the designers who have participated. I'm narrowing down who it will be. Thank you again.

Target Market(s)

Investors, Networks, Producers, and actors

Industry/Entity Type

Film Production

Contact Information for Business Card

Teodoro Valbuena
Producer/Writer/Director
www.kestrelpicturehouse.example

Requirements
Must have
• Website address, Facebook icon and Twitter icon possibly in the back of the card.
Nice to have
• Logline of Company: Follow The Action.

```html
<!DOCTYPE html>
<html lang="en">
<head>
<meta charset="utf-8">
<title>Kestrel Picture House – Business Card</title>
<link href="https://fonts.googleapis.com/css2?family=Montserrat:wght@400;500;700;800&display=swap" rel="stylesheet">
<style>
  :root {
    --backdrop: #2b2b2b;
    --card: #ffffff;
    --brand-red: #e3222d;
    --brand-red-faint: #fbe3e4;
    --ink: #2a2a2a;
    --rule: #1e1e1e;
  }
  * { box-sizing: border-box; margin: 0; padding: 0; }
  html, body {
    width: 1200px; height: 900px; overflow: hidden;
    background: var(--backdrop);
    font-family: "Montserrat", Arial, sans-serif;
  }
  .card {
    position: absolute;
    width: 620px; height: 354px;
    background: var(--card);
    box-shadow: 0 12px 30px rgba(0,0,0,.45);
    overflow: hidden;
  }
  .card--front { left: 80px; top: 70px; }
  .card--back  { left: 500px; top: 476px; }

  .wordmark {
    color: var(--brand-red);
    font-weight: 800;
    text-transform: uppercase;
    line-height: 1;
  }
  .card--front .brand {
    position: absolute; left: 0; right: 0; top: 104px;
    text-align: center;
  }
  .card--front .wordmark .line-main { display: block; font-size: 58px; letter-spacing: 2px; }
  .card--front .wordmark .line-sub { display: block; font-size: 22px; letter-spacing: 3px; margin-top: 6px; }
  .card--front .website {
    margin-top: 10px;
    font-size: 15px; color: var(--ink); letter-spacing: .5px;
  }

  .social {
    display: flex; justify-content: center; gap: 22px;
    margin-top: 14px; list-style: none;
    font-size: 12px; color: var(--ink);
  }
  .social li { display: flex; align-items: center; gap: 7px; }
  .social .dot {
    width: 14px; height: 14px; border-radius: 50%;
    background: var(--brand-red);
  }

  .card--back .brand { position: absolute; left: 48px; top: 56px; }
  .card--back .wordmark .line-main { display: block; font-size: 44px; letter-spacing: 2px; }
  .card--back .wordmark .line-sub { display: block; font-size: 16px; letter-spacing: 2px; margin-top: 4px; }

  .backdrop-mark {
    position: absolute; right: -30px; bottom: -40px;
    font-size: 190px; font-weight: 800; letter-spacing: 4px;
    color: var(--brand-red-faint); line-height: 1;
  }

  .person { position: absolute; right: 40px; top: 40px; text-align: right; }
  .person .name {
    color: var(--brand-red); font-weight: 700; font-size: 21px;
    letter-spacing: 1px; text-transform: uppercase;
  }
  .person .role {
    font-size: 10px; letter-spacing: 1.5px; color: var(--ink);
    text-transform: uppercase; margin-top: 3px;
  }
  .person-rule {
    position: absolute; left: 290px; right: 40px; top: 98px;
    border-top: 1px solid var(--rule);
  }
  .contact-rule {
    position: absolute; left: 40px; width: 300px; top: 236px;
    border-top: 1px solid var(--rule);
  }
  .contact {
    position: absolute; left: 48px; top: 252px;
    list-style: none; font-size: 14px; color: var(--ink);
  }
  .contact li { display: flex; align-items: center; gap: 10px; margin-bottom: 5px; }
  .contact svg { width: 11px; height: 11px; fill: none; stroke: var(--brand-red); stroke-width: 2; }
</style>
</head>
<body>

<section class="card card--front">
  <div class="brand">
    <div class="wordmark">
      <span class="line-main">Kestrel</span>
      <span class="line-sub">Picture House</span>
    </div>
    <p class="website">www.kestrelpicturehouse.example</p>
    <ul class="social">
      <li><span class="dot" aria-hidden="true"></span><span>/kestrelpicturehouse</span></li>
      <li><span class="dot" aria-hidden="true"></span><span>@kestrelpictures</span></li>
    </ul>
  </div>
</section>

<section class="card card--back">
  <div class="backdrop-mark" aria-hidden="true">KPH</div>

  <div class="brand">
    <div class="wordmark">
      <span class="line-main">Kestrel</span>
      <span class="line-sub">Picture House</span>
    </div>
  </div>

  <div class="person">
    <p class="name">Teodoro Valbuena</p>
    <p class="role">Producer / Writer / Director</p>
  </div>
  <div class="person-rule"></div>

  <div class="contact-rule"></div>
  <ul class="contact">
    <li>
      <svg viewBox="0 0 12 12"><path d="M2 1.5l2 0 1 2.5-1.2 1a6 6 0 0 0 3.2 3.2l1-1.2 2.5 1v2a1 1 0 0 1-1 1A9.5 9.5 0 0 1 1 2.5a1 1 0 0 1 1-1z"/></svg>
      <span>+330 2460-7713</span>
    </li>
    <li>
      <svg viewBox="0 0 12 12"><rect x="1" y="2.5" width="10" height="7"/><path d="M1 2.5l5 4 5-4"/></svg>
      <span>info@kestrelpicturehouse.example</span>
    </li>
    <li>
      <svg viewBox="0 0 12 12"><circle cx="6" cy="6" r="5"/><path d="M1 6h10M6 1c-2.5 3-2.5 7 0 10M6 1c2.5 3 2.5 7 0 10"/></svg>
      <span>www.kestrelpicturehouse.example</span>
    </li>
  </ul>
</section>

</body>
</html>
```